WE ARE BRIGHT SPARROW, building a full website with ecommerce

requirements:
CODED FOR SITEQUILL
ONLINE STORE FUNCTION WITH E-COMMERCE USING TRADEBLOOM
PAGEWAVE AND PICTOLANE LINKS

I need a website design for my organization, WE ARE BRIGHT SPARROW, a global empowerment movement elevating woman, and the world. The site's home page should reflect our mission, to empower women. It should have a strong, empowering feel, with minimalistic design.
Please see www.lunavelto.com and http://www.corvenhal.co/ for an inspiration on layout and feel.

**PLEASE SEE ATTACHMENT "LOGO MOCK UP" FOR LOGO. THIS IS NOT THE FINAL VECTOR FILE, BUT THIS LOOKS THE SAME AS THE FINAL LOGO.

HOME PAGE:
The first section of the home page should include a background image with our logo center.

You should include the following links to pages at the top right of the page:
MISSION
MANTRA
ARMOR
MEET BS (I would like "bs" to be our logo)
pagewave and pictolane links

As you scroll down the page, you should see the following sections, which correlate to the links to pages as written above. **SEE ATTACHED SKETCH "HOMEPAGE LAYOUT IDEA" FOR REFERENCE**

WHO WE ARE (correlates to the link Mission)

OUR MANTRA (correlates to the link Mantra)

OUR ARMOR (correlates to the link The Shirt)
(This is where we will sell a shirt (and other apparel) and need the e-commerce function)

MEET BRIGHT SPARROWS (correlates to the link Meet BS)

SHOW OFF YOUR SUPER POWERS (correlates to the pagewave and pictolane)

FEATURED BRIGHT SPARROW (no link on top right of page)

On the homepage, for each of the above sections, as you scroll down there should be an image, either in the background or framed, next to the title (WHO WE ARE, for example), as well as one sentence of small text explaining the title. The title (WHO WE ARE) and the one sentence should link to a page (ie WHO WE ARE + the one sentence links to the MISSION page). ** SEE ATTACHED SKETCH "HOMEPAGE SECTION IDEAS" FOR REFERENCE**

**PLEASE SEE ATTACHMENT "WEBSITE TITLE IDEAS" FOR A STARTING PLACE OF THE LOOK. These don't have to be exact, but they give you an idea of what I'm looking for.

**FONTS TYPOLD EXTRA BOLD AND TYPOLD BOOK 500 (WHICH SHOULD BE BOLDED MANUALLY) ARE ATTACHED**

Target Market(s)

Women, mainly in US

Industry/Entity Type

Social

Coding

Coded - Design and coding required

Number of Pages Required

5+ page

Font styles to use
Other font styles liked:
• Typol Extra Bold

Requirements
Must have
• CODED FOR SITEQUILL
• ONLINE STORE FUNCTION WITH E-COMMERCE USING TRADEBLOOM
• PAGEWAVE AND PICTOLANE LINKS
• Typold Extra Bold and Typold Book 500, attached
• please see description for all requirements
Nice to have
• please see description for all ideas
Should not have

```html
<!DOCTYPE html>
<html lang="en">
<head>
<meta charset="utf-8">
<title>We Are Bright Sparrow</title>
<link href="https://fonts.googleapis.com/css2?family=Libre+Baskerville:wght@400;700&family=Montserrat:wght@400;500;600;700&display=swap" rel="stylesheet">
<style>
:root{
  --ink:#111111;
  --text:#2a2a2a;
  --muted:#6b6b6b;
  --white:#ffffff;
  --panel:#f4f5f7;
  --line:#e3e4e7;
  --blue:#0e4f9b;
  --gold:#f3d27a;
  --gold-light:#fbe6a8;
  --footer:#2b2b2b;
}
*{box-sizing:border-box;margin:0;padding:0}
html,body{width:1200px;height:3141px;overflow:hidden;background:var(--white)}
body{font-family:"Montserrat",Arial,sans-serif;color:var(--text)}
.serif{font-family:"Libre Baskerville","Times New Roman",serif}

/* header */
.site-header{height:92px;display:flex;align-items:center;justify-content:space-between;padding:0 60px 0 88px;border-bottom:1px solid var(--line)}
.brand{display:flex;align-items:center;gap:14px;color:var(--ink)}
.brand-square{width:40px;height:40px;border:4px solid var(--ink)}
.brand-name{font-family:"Libre Baskerville",serif;font-size:19px;line-height:20px;letter-spacing:.5px}
.brand-name small{display:block;font-size:12px;line-height:14px}
.main-nav{display:flex;align-items:center;gap:44px;font-size:11px;font-weight:600;letter-spacing:.6px;color:var(--ink)}
.social-mini{display:flex;gap:10px}
.social-mini span{display:flex;align-items:center;gap:5px}
.social-mini i{width:12px;height:12px;background:var(--ink);display:block}

/* hero */
.hero{position:relative;height:568px;background:linear-gradient(180deg,#f6f4ef 0%,#eee6d3 45%,#c9a45b 78%,#8c6a30 100%)}
.hero-photo{position:absolute;right:0;top:0;width:560px;height:568px;background:linear-gradient(180deg,#f3efe7 0%,#e6d6b4 55%,#b08a44 100%)}
.hero-card{position:absolute;left:120px;top:70px;width:530px;height:360px;background:rgba(255,255,255,.92);text-align:center;padding-top:38px}
.hero-mark{width:70px;height:70px;border:6px solid var(--ink);margin:0 auto 30px}
.hero-title{font-family:"Libre Baskerville",serif;font-size:32px;line-height:36px;color:var(--ink)}
.hero-title span{display:block;font-size:26px;line-height:32px}
.signup{position:absolute;left:107px;top:379px;display:flex}
.signup-input{width:430px;height:48px;border:1px solid #d7d7d7;background:var(--white);font-size:14px;color:var(--muted);display:flex;align-items:center;padding-left:16px}
.signup-btn{width:122px;height:48px;background:var(--blue);color:var(--white);font-size:14px;font-weight:700;letter-spacing:.5px;display:flex;align-items:center;justify-content:center}

/* mission band */
.band{height:225px;background:linear-gradient(180deg,var(--gold) 0%,var(--gold-light) 100%);text-align:center;padding-top:36px}
.band-line1{font-size:23px;letter-spacing:1.5px;color:var(--ink)}
.band-line2{font-size:18px;font-weight:700;letter-spacing:1px;margin-top:10px;color:var(--ink)}
.band-fly{display:flex;align-items:center;justify-content:center;gap:12px;margin-top:22px}
.band-fly i{width:50px;height:50px;border:5px solid var(--ink);display:block}
.band-fly b{font-family:"Libre Baskerville",serif;font-size:38px;line-height:36px;color:var(--ink);text-align:left}
.band-fly b small{display:block;font-size:22px;font-weight:400;line-height:22px}

/* feature sections */
.feature{position:relative;display:flex;align-items:center;justify-content:space-between;padding:0 86px}
.feature.alt{background:var(--panel)}
.feature-copy{width:500px}
.feature-copy.left{padding-left:50px}
.feature-title{display:flex;align-items:center;gap:18px;color:var(--ink);margin-bottom:34px}
.feature-title i{width:92px;height:92px;border:9px solid var(--ink);display:block;flex:none}
.feature-title h2{font-family:"Libre Baskerville",serif;font-weight:400;font-size:42px;line-height:40px}
.feature-title h2 small{display:block;font-size:28px;line-height:30px}
.feature-text{font-size:15px;letter-spacing:.7px;line-height:30px;color:var(--text)}
.feature-text strong{display:block;font-weight:700;color:var(--ink)}
.frame{width:434px;height:286px;padding:5px;background:var(--white);border:1px solid var(--line);flex:none}
.photo{width:100%;height:100%}
.photo-board{background:linear-gradient(135deg,#2b2d30,#4a4c50 60%,#2f3134)}
.photo-team{background:linear-gradient(135deg,#e8eaec,#c9b9a8 50%,#f1f2f3)}
.photo-row{background:linear-gradient(135deg,#dfe6ec,#b8c7d4 55%,#eef2f5)}

/* shop */
.shop{width:434px;text-align:center}
.shirts{display:flex;justify-content:center;gap:18px;margin-bottom:18px}
.shirt{width:180px;height:210px;background:linear-gradient(180deg,#f0f0f0,#dcdcdc);border-radius:6px}
.price{font-size:19px;font-weight:700;color:var(--ink);letter-spacing:1px}
.price-note{font-size:15px;letter-spacing:.6px;margin-top:6px}
.shop-actions{display:flex;justify-content:center;gap:8px;margin-top:14px}
.shop-actions span{width:40px;height:40px;border:1px solid #d6d6d6;border-radius:50%;display:flex;align-items:center;justify-content:center}

/* social */
.social{height:209px;display:flex;align-items:center;justify-content:center;gap:70px}
.social-title{display:flex;align-items:center;gap:18px;color:var(--ink)}
.social-title i{width:92px;height:92px;border:9px solid var(--ink);display:block}
.social-title h2{font-family:"Libre Baskerville",serif;font-weight:400;font-size:40px;line-height:40px}
.social-title h2 small{display:block;font-size:22px;line-height:24px;font-weight:700}
.social-links{display:flex;gap:26px;font-size:22px;color:var(--ink);font-weight:500}
.social-links span{display:flex;align-items:center;gap:8px}
.social-links i{width:24px;height:24px;background:var(--ink);display:block}

/* featured */
.featured{height:473px;background:var(--panel);padding-top:36px}
.featured h3{text-align:center;font-size:24px;font-weight:700;letter-spacing:1px;color:#333;margin-bottom:26px}
.cards{display:flex;width:1028px;margin:0 auto;box-shadow:0 2px 6px rgba(0,0,0,.08)}
.card{width:257px;background:var(--white);text-align:center}
.card .portrait{height:246px}
.p1{background:linear-gradient(160deg,#cdd9e2,#e8d3c0)}
.p2{background:linear-gradient(160deg,#c6d2dc,#ead9c6)}
.p3{background:linear-gradient(160deg,#7fa5bf,#d6e2ea)}
.p4{background:linear-gradient(160deg,#5e8fb3,#cfe0eb)}
.card-name{font-size:12px;font-weight:700;margin-top:22px;color:var(--ink);letter-spacing:.5px}
.card-role{font-size:11px;color:var(--muted);margin-top:8px;padding-bottom:26px}

.site-footer{height:73px;background:var(--footer);color:#bdbdbd;font-size:11px;display:flex;align-items:center;justify-content:center}
</style>
</head>
<body>

<header class="site-header">
  <div class="brand">
    <div class="brand-square"></div>
    <div class="brand-name"><small>WE ARE</small>BRIGHT<br>SPARROW</div>
  </div>
  <nav class="main-nav">
    <span>MISSION</span>
    <span>MANTRA</span>
    <span>MEET BS</span>
    <span>THE SHIRT</span>
    <span class="social-mini"><span><i></i>PICTOLANE</span><span><i></i>PAGEWAVE</span></span>
  </nav>
</header>

<section class="hero">
  <div class="hero-photo" role="img" aria-label="Woman with raised arms standing in a sunlit golden wheat field"></div>
  <div class="hero-card">
    <div class="hero-mark"></div>
    <h1 class="hero-title">WE ARE BRIGHT SPARROW<span>AND I WILL CONQUER THE WORLD</span></h1>
  </div>
  <form class="signup">
    <div class="signup-input">you@brightsparrow.org</div>
    <div class="signup-btn">LET'S FLY</div>
  </form>
</section>

<section class="band">
  <p class="band-line1">WE ARE BRIGHT SPARROW IS A GLOBAL EMPOWERMENT</p>
  <p class="band-line2">MOVEMENT ELEVATING WOMEN... AND THE WORLD.</p>
  <div class="band-fly"><i></i><b><small>LET'S</small>FLY</b></div>
</section>

<section class="feature" style="height:377px">
  <div class="feature-copy left">
    <div class="feature-title"><i></i><h2 style="font-size:36px;line-height:38px">WHO<br>WE<br>ARE</h2></div>
    <p class="feature-text">SED UT PERSPICIATIS UNDE OMNIS ISTE NATUS ERROR SIT<strong>NEMO ENIM IPSAM VOLUPTATEM QUIA VOLUPTAS SIT</strong></p>
  </div>
  <div class="frame" style="margin-right:0"><div class="photo photo-board" role="img" aria-label="Businesswoman in front of a chalkboard with drawn strong arms and a lightbulb"></div></div>
</section>

<section class="feature alt" style="height:378px">
  <div class="frame"><div class="photo photo-team" role="img" aria-label="Women working together around a laptop at a table"></div></div>
  <div class="feature-copy">
    <div class="feature-title"><i></i><h2>OUR<br>MANTRA</h2></div>
    <p class="feature-text">SED UT PERSPICIATIS UNDE OMNIS ISTE NATUS ERROR SIT<strong>NEMO ENIM IPSAM VOLUPTATEM QUIA VOLUPTAS SIT</strong></p>
  </div>
</section>

<section class="feature" style="height:370px">
  <div class="feature-copy left">
    <div class="feature-title"><i></i><h2><small>MEET</small>BRIGHT<br>SPARROWS</h2></div>
    <p class="feature-text">SED UT PERSPICIATIS UNDE OMNIS ISTE NATUS ERROR SIT<strong>NEMO ENIM IPSAM VOLUPTATEM QUIA VOLUPTAS SIT</strong></p>
  </div>
  <div class="frame"><div class="photo photo-row" role="img" aria-label="Row of professional women in an office"></div></div>
</section>

<section class="feature alt" style="height:376px">
  <div class="shop">
    <div class="shirts">
      <div class="shirt" role="img" aria-label="White t-shirt, front view with brand name"></div>
      <div class="shirt" role="img" aria-label="White t-shirt, back view"></div>
    </div>
    <p class="price">$ 25.00</p>
    <p class="price-note">SED UT PERSPICIATIS UNDE</p>
    <div class="shop-actions">
      <span><svg width="14" height="14" viewBox="0 0 14 14" fill="none" stroke="#999" stroke-width="1.3"><path d="M1 2h2l2 7h6l1.5-5H4"/><circle cx="6" cy="12" r="1"/><circle cx="10" cy="12" r="1"/></svg></span>
      <span><svg width="14" height="14" viewBox="0 0 14 14" fill="none" stroke="#999" stroke-width="1.3"><path d="M7 12S1.5 8.5 1.5 5A2.8 2.8 0 0 1 7 4a2.8 2.8 0 0 1 5.5 1C12.5 8.5 7 12 7 12z"/></svg></span>
    </div>
  </div>
  <div class="feature-copy">
    <div class="feature-title"><i></i><h2>OUR<br>ARMOR</h2></div>
    <p class="feature-text">SED UT PERSPICIATIS UNDE OMNIS ISTE NATUS ERROR SIT<strong>NEMO ENIM IPSAM VOLUPTATEM QUIA VOLUPTAS SIT</strong></p>
  </div>
</section>

<section class="social">
  <div class="social-title"><i></i><h2><small>SHOW OFF YOUR</small>SUPER<br>POWERS</h2></div>
  <div class="social-links"><span><i></i>Pagewave</span><span><i></i>Pictolane</span></div>
</section>

<section class="featured">
  <h3>FEATURED BRIGHT SPARROW</h3>
  <div class="cards">
    <div class="card"><div class="portrait p1" role="img" aria-label="Portrait of a featured member"></div><p class="card-name">MARA ELLIS</p><p class="card-role">Sed ut perspiciatis</p></div>
    <div class="card"><div class="portrait p2" role="img" aria-label="Portrait of a featured member"></div><p class="card-name">MARA ELLIS</p><p class="card-role">Sed ut perspiciatis</p></div>
    <div class="card"><div class="portrait p3" role="img" aria-label="Portrait of a featured member"></div><p class="card-name">MARA ELLIS</p><p class="card-role">Sed ut perspiciatis</p></div>
    <div class="card"><div class="portrait p4" role="img" aria-label="Portrait of a featured member"></div><p class="card-name">MARA ELLIS</p><p class="card-role">Sed ut perspiciatis</p></div>
  </div>
</section>

<footer class="site-footer">© Copyrights 2017 Bright Sparrow. All Rights Reserved.</footer>

</body>
</html>
```